KTWG application splash screen

We need a 1024x768 image for use as an application splash screen.
The image will be displayed full screen on an 10 inch industrial PC 1024x768 screen while our application is launching. The image should convey that the application is "Waiting for connection to Wi-Fi access point..." and include a graphic of the industrial PC connected to the access point via an Ethernet cable. A list of troubleshooting steps should be included at the bottom of the image. The troubleshooting steps should not be the main focus of the image and should be shown in a smaller font (but still readable at 1024x768 displayed on a 10 inch screen).
I will include a mock up of the general idea of what we are looking for as well as image files for the industrial PC, a screenshot of our application to show on the PC's screen and the AP.
For general look and feel and a sense of corporate branding please review our website https://marrowgatesoilworks.example/. The splash screen should reflect corporate branding.
Target Market(s)
Users of our application
Industry/Entity Type
Agriculture
Look and feel

```html
<!DOCTYPE html>
<html lang="en">
<head>
<meta charset="utf-8">
<title>KTWG – Waiting for Wi-Fi access point</title>
<link rel="stylesheet" href="https://fonts.googleapis.com/css2?family=Barlow:wght@400;500;600&family=Barlow+Semi+Condensed:wght@400;600&display=swap">
<style>
  :root {
    --brand-green: #2bb673;
    --paper: #ffffff;
    --ink: #111111;
    --device-dark: #2a2a2a;
    --ap-light: #f1f1f1;
    --ap-shade: #d9d9d9;
  }
  * { margin: 0; padding: 0; box-sizing: border-box; }
  html, body { width: 1200px; height: 900px; overflow: hidden; background: var(--paper); }
  .splash {
    position: relative;
    width: 1200px;
    height: 900px;
    overflow: hidden;
    font-family: "Barlow", Arial, sans-serif;
    background: var(--paper);
  }
  .backdrop { position: absolute; inset: 0; }
  .headline {
    position: absolute;
    left: 0;
    top: 30px;
    width: 810px;
    text-align: center;
    color: var(--paper);
    font-weight: 500;
    font-size: 73px;
    line-height: 82px;
  }
  .label-computer {
    position: absolute;
    left: 91px;
    top: 645px;
    width: 317px;
    text-align: center;
    color: var(--brand-green);
    font-weight: 500;
    font-size: 21px;
  }
  .label-ap {
    position: absolute;
    left: 947px;
    top: 617px;
    width: 178px;
    text-align: center;
    color: var(--paper);
    font-weight: 500;
    font-size: 19px;
    line-height: 24px;
    letter-spacing: 0.5px;
  }
  .brand-name {
    position: absolute;
    left: 947px;
    top: 700px;
    width: 174px;
    height: 170px;
    display: flex;
    align-items: center;
    justify-content: center;
    color: var(--paper);
    font-weight: 600;
    font-size: 40px;
    letter-spacing: 1px;
  }
  .troubleshooting {
    position: absolute;
    left: 86px;
    top: 697px;
    width: 799px;
    height: 172px;
    border-radius: 54px;
    background: var(--brand-green);
    color: var(--paper);
    padding: 18px 12px 0 29px;
    font-family: "Barlow Semi Condensed", "Barlow", Arial, sans-serif;
  }
  .troubleshooting h2 {
    font-size: 12.5px;
    font-weight: 600;
    line-height: 18px;
    margin-bottom: 8px;
  }
  .steps { list-style: none; font-size: 12.5px; line-height: 18px; }
  .steps > li { padding-left: 20px; position: relative; white-space: nowrap; }
  .steps > li::before { content: "➤"; position: absolute; left: 0; }
  .substeps { list-style: none; padding-left: 3px; }
  .substeps li { position: relative; padding-left: 12px; white-space: nowrap; }
  .substeps li::before { content: "➡"; position: absolute; left: 0; font-size: 9px; }
</style>
</head>
<body>
<main class="splash">
  <svg class="backdrop" width="1200" height="900" viewBox="0 0 1024 768">
    <path d="M0 0 H1024 V104 H830 C770 104 735 130 705 180 C680 225 655 265 610 265 H0 Z" fill="var(--brand-green)"/>
    <path d="M808 104 V620 H960 V104 Z" fill="var(--brand-green)"/>
    <rect x="792" y="580" width="182" height="178" rx="42" fill="var(--paper)"/>
    <rect x="808" y="597" width="148" height="145" rx="34" fill="var(--brand-green)"/>
    <path d="M346 512 H868 Q884 512 884 496 V462" fill="none" stroke="var(--ink)" stroke-width="3.5" stroke-linecap="round"/>
    <defs>
      <linearGradient id="apGradient" x1="0" x2="1">
        <stop offset="0" stop-color="var(--ap-shade)"/>
        <stop offset="0.5" stop-color="var(--ap-light)"/>
        <stop offset="1" stop-color="var(--ap-shade)"/>
      </linearGradient>
    </defs>
    <rect x="78" y="330" width="270" height="208" rx="10" fill="var(--device-dark)" role="img" aria-label="Industrial tractor cab computer showing the seeding application screen"/>
    <rect x="870" y="125" width="30" height="340" rx="12" fill="url(#apGradient)" role="img" aria-label="Outdoor Wi-Fi access point with antennas"/>
  </svg>

  <h1 class="headline">Waiting for<br>connection to Wi-Fi<br>access point...</h1>

  <p class="label-computer">Tractor Cab Computer</p>
  <p class="label-ap">Wi-Fi Access<br>Point</p>
  <div class="brand-name">KTWG</div>

  <section class="troubleshooting">
    <h2>Troubleshooting steps:</h2>
    <ul class="steps">
      <li>This screen should only be visible for a short time on boot.</li>
      <li>If this screen stays visible for more than a minute:
        <ul class="substeps">
          <li>Verify that the Wi-Fi Access Point (AP) powers up when this system does (indicated by a green light on the side of the AP).</li>
          <li>Check the Ethernet cable between this system and the AP for damage, and replace it if necessary.</li>
          <li>Power-cycle this system and wait for it to reboot fully.</li>
          <li>If the issue persists, contact KTWG support for further assistance.</li>
        </ul>
      </li>
    </ul>
  </section>
</main>
</body>
</html>
```